Business Card Design Project

double sided, embossed, name & logo on front font sonsie one, back Name Marisa Dobrowen, mobile 0468214073, Phone 86190357,
email marisa@brightsweepco.com, use sysbols on the back for example an envelope for email, a telephone for phone number etc.symbol slate grey writing navy blue

Industry/Entity Type

Business

```html
<!DOCTYPE html>
<html lang="en">
<head>
<meta charset="UTF-8">
<title>Bright Sweep Co — Business Card</title>
<link rel="stylesheet" href="https://fonts.googleapis.com/css2?family=Open+Sans:wght@400;600&display=swap">
<style>
  :root {
    --backdrop: #e4e6e9;
    --card: #ffffff;
    --navy: #1f5a8c;
    --slate: #5a6672;
    --emboss: #eef0f2;
    --card-shadow: rgba(20, 30, 45, 0.18);
  }
  * { box-sizing: border-box; margin: 0; padding: 0; }
  html, body {
    width: 1200px;
    height: 900px;
    overflow: hidden;
    background: var(--backdrop);
    font-family: "Open Sans", Arial, sans-serif;
  }
  .canvas {
    width: 1200px;
    height: 900px;
    display: flex;
    flex-direction: column;
    align-items: center;
    justify-content: center;
    gap: 40px;
  }
  .card {
    position: relative;
    width: 700px;
    height: 400px;
    background: var(--card);
    box-shadow: 0 6px 22px var(--card-shadow);
  }

  /* Front */
  .card--front .brand {
    position: absolute;
    left: 0; right: 0; top: 0; bottom: 0;
    display: flex;
    align-items: center;
    justify-content: center;
    gap: 18px;
  }
  .brand__dot {
    width: 30px;
    height: 30px;
    border-radius: 50%;
    background: var(--navy);
  }
  .brand__name {
    font-size: 56px;
    font-weight: 600;
    color: var(--navy);
    letter-spacing: 0.5px;
  }

  /* Back */
  .holder-name {
    position: absolute;
    left: 82px;
    top: 92px;
    font-size: 24px;
    font-weight: 400;
    color: var(--navy);
  }
  .emboss-mark {
    position: absolute;
    left: 0; right: 0;
    top: 150px;
    text-align: center;
    font-size: 50px;
    font-weight: 600;
    color: var(--emboss);
    text-shadow: 0 1px 0 #ffffff;
  }
  .contact-list {
    position: absolute;
    left: 320px;
    top: 224px;
    list-style: none;
  }
  .contact-list li {
    display: flex;
    align-items: center;
    gap: 12px;
    height: 30px;
    font-size: 19px;
    color: var(--navy);
  }
  .contact-list svg {
    width: 16px;
    height: 16px;
    fill: var(--slate);
    flex: none;
  }
</style>
</head>
<body>
<main class="canvas">

  <section class="card card--front" aria-label="Card front">
    <div class="brand">
      <span class="brand__dot"></span>
      <span class="brand__name">Bright Sweep Co</span>
    </div>
  </section>

  <section class="card card--back" aria-label="Card back">
    <p class="holder-name">Marisa Dobrowen</p>
    <p class="emboss-mark" aria-hidden="true">Bright Sweep Co</p>
    <ul class="contact-list">
      <li>
        <svg viewBox="0 0 16 16" aria-label="Mobile"><rect x="4" y="1" width="8" height="14" rx="1.5"/><rect x="5.5" y="3" width="5" height="8" fill="#fff"/><circle cx="8" cy="13" r="0.9" fill="#fff"/></svg>
        <span>0468 214 073</span>
      </li>
      <li>
        <svg viewBox="0 0 16 16" aria-label="Phone"><circle cx="8" cy="8" r="7.5"/><path d="M5.2 4c.4-.3.9-.2 1.1.2l.7 1.4c.2.4 0 .7-.3.9l-.5.3c.4 1.1 1.2 2 2.3 2.6l.4-.5c.2-.3.6-.4.9-.2l1.4.8c.4.2.5.7.2 1.1-.6.8-1.5 1-2.3.7C7 10.5 5.3 8.7 4.6 6.5c-.3-.9 0-1.9.6-2.5z" fill="#fff"/></svg>
        <span>8619 0357</span>
      </li>
      <li>
        <svg viewBox="0 0 16 16" aria-label="Email"><rect x="1" y="3" width="14" height="10" rx="1"/><path d="M1.8 4l6.2 5 6.2-5" fill="none" stroke="#fff" stroke-width="1.2"/></svg>
        <span>marisa@brightsweepco.com</span>
      </li>
      <li>
        <svg viewBox="0 0 16 16" aria-label="Address"><path d="M8 1.5L1 8h2v6.5h4v-4h2v4h4V8h2z"/></svg>
        <span>47 Harbour Tce Largs Bay 5016</span>
      </li>
    </ul>
  </section>

</main>
</body>
</html>
```